Oliver + Rory's 30th Birthday FB event cover photo

We're after a Facebook even cover photo for our 30th B'day. We live in Sydney
Oliver + Rory's 30th Birthday

Venue (these details can be used in the graphic):
Quiet Heron
the basement of
The Walrus Hotel
214 Corran St Halvey
2 August 8pm-3am

The Walrus logo: http://www.thewalrushotel.example
Quiet Heron logo: http://quietheronpurr.example.au
The horizontal FaceBook cover photo for events has specific dimensions
As ideas I kind of like the styling of the dj poster (file attached) as a rough guide but not essential (i.e. no need to stick to that format/colours/dark shades) and Also the poster Pixel Bazaar's Morven did for Velvet Drift
Thanks!

```html
<!DOCTYPE html>
<html lang="en">
<head>
<meta charset="utf-8">
<title>Oliver &amp; Rory's 30th Birthday</title>
<link rel="stylesheet" href="https://fonts.googleapis.com/css2?family=Josefin+Sans:wght@300;700&display=swap">
<style>
  :root {
    --cream: #f2e4cf;
    --tan: #c9ab8c;
    --orange: #f08d28;
    --brown-dark: #3e2618;
    --brown-mid: #7a4a2b;
    --peach: #e9c39a;
    --amber: #d9701f;
  }
  html, body {
    margin: 0;
    padding: 0;
    overflow: hidden;
    background: #1a1008;
  }
  .cover {
    position: relative;
    width: 1200px;
    height: 443px;
    overflow: hidden;
    font-family: "Josefin Sans", sans-serif;
  }
  .cover__backdrop {
    position: absolute;
    inset: 0;
    background:
      radial-gradient(ellipse 420px 260px at 18% 20%, rgba(215,170,125,0.75), transparent 70%),
      radial-gradient(ellipse 380px 300px at 90% 25%, rgba(236,200,160,0.85), transparent 70%),
      radial-gradient(ellipse 520px 220px at 30% 100%, rgba(232,120,40,0.9), transparent 70%),
      radial-gradient(ellipse 420px 260px at 88% 95%, rgba(230,110,30,0.8), transparent 70%),
      radial-gradient(ellipse 380px 300px at 58% 45%, rgba(50,30,18,0.9), transparent 75%),
      linear-gradient(135deg, var(--brown-mid) 0%, var(--brown-dark) 50%, var(--amber) 100%);
  }
  .event-title {
    position: absolute;
    left: 34px;
    top: 36px;
    margin: 0;
    color: var(--cream);
    font-weight: 700;
    font-size: 96px;
    line-height: 84px;
    letter-spacing: 3px;
    text-transform: uppercase;
    opacity: 0.92;
  }
  .event-venue {
    position: absolute;
    left: 36px;
    top: 224px;
    margin: 0;
    color: var(--tan);
    font-weight: 300;
    font-size: 19px;
    letter-spacing: 1.5px;
    text-transform: uppercase;
    word-spacing: 2px;
  }
  .event-venue__gap { display: inline-block; width: 18px; }
  .event-time {
    position: absolute;
    left: 34px;
    top: 254px;
    margin: 0;
    color: var(--orange);
    font-weight: 700;
    font-size: 44px;
    letter-spacing: 1px;
    text-transform: uppercase;
  }
  .host-name {
    position: absolute;
    right: 40px;
    top: 378px;
    margin: 0;
    color: var(--orange);
    font-weight: 700;
    font-size: 36px;
    letter-spacing: 3px;
    text-transform: uppercase;
  }
</style>
</head>
<body>
  <main class="cover">
    <div class="cover__backdrop" role="img" aria-label="Abstract backdrop of overlapping translucent rectangles in cream, brown and orange tones"></div>
    <h1 class="event-title">Oliver &amp; Rory's<br>30th Birthday</h1>
    <p class="event-venue">214 Corran St Halvey<span class="event-venue__gap"></span>The Basement of the Walrus Hotel</p>
    <p class="event-time">2 August 8pm - 3am</p>
    <p class="host-name">Quiet Heron</p>
  </main>
</body>
</html>
```